Hop Bright Meadow Business Website Branding

Looking for a wordpress template design with CSS and HTML encoding. Current website can be seen at hopbrightmeadow.example.

WE ARE CURRENTLY IN PROCESS GETTING A LOGO DESIGN... I HAVE INCLUDED THE TOP POTENTIAL DESIGNS FOR REFERENCE TO HELP UNDERSTAND WHAT STYLE WE ARE LOOKING FOR...
NOTE: THE “PEBBLE CREW” LOGO WAS A PREVIOUS COMPANY WE OWNED SO YOU CAN GE A FEEL FOR THE TYPE OF DESIGNS WE HAVE USED IN THE PAST.

My blog will focus on making a connection with wild Florida, it’s wildlife, plants and animals... with an eye toward Florida conservation, nature adventure trips, and education... Content, photos and other merchandise will also be offered for sale.
I’m looking for a site design that incorporates Florida nature and wildlife/plants, with a fun “Old Florida” retro-adventure feel.
When they see this site it should speak to the import of natural Florida and the critical nature of the ecosystem here... while being instantly recognizable and iconic... IE: when I think of florida I think of water, plants, warmth, sunsets etc...

https://join.chatroomhub.example/t/lumexstudio-kzt4821/shared_invite/zt-pqwrt83m-hRnLvXaKoPzsYcB1Uq7JdM

Target Market(s)

Nature, Education, Conservation, Photography

Industry/Entity Type

Photographer

Coding

Coded - Design and coding required

Requirements
Must have
• Need to have site wide template design which generally includes a landing page and a general page template for other pages... Must include html and css encoding...
Should not have
• Any animals included in the site should be Florida native... IE: no African animals etc... This will require some research to ensure that if animals are included that they are part of the Florida ecosystem.

```html
<!DOCTYPE html>
<html lang="en">
<head>
<meta charset="utf-8">
<title>Hop Bright Meadow! – Exploring Florida's Natural Wonders</title>
<link rel="stylesheet" href="https://fonts.googleapis.com/css2?family=Poppins:wght@500;600;700&family=Libre+Baskerville&family=Overpass:wght@400;600;700&display=swap">
<style>
:root{
  --paper:#f6e6c4;
  --paper-light:#fbf0d8;
  --paper-dark:#ecd3a3;
  --ink:#1d1a15;
  --text:#3a332a;
  --brown:#7a5a2e;
  --frame:#b9a27c;
  --white:#ffffff;
  --card:#fffdf8;
}
*{box-sizing:border-box;margin:0;padding:0}
html,body{width:1200px;height:3052px;overflow:hidden}
body{font-family:"Overpass",sans-serif;color:var(--text);
  background:radial-gradient(ellipse at 50% 40%,var(--paper-light) 0%,var(--paper) 55%,var(--paper-dark) 100%)}
.page{position:relative;width:1200px;height:3052px;overflow:hidden}
.abs{position:absolute}
.brand-mark{position:absolute;width:54px;height:54px;border-radius:50%;background:var(--brown)}
.brand-name{position:absolute;font-family:"Poppins",sans-serif;font-weight:700;font-size:25px;color:var(--ink);white-space:nowrap}
.brand-tag{position:absolute;font-size:14px;color:var(--ink);white-space:nowrap}
.follow{position:absolute;display:flex;align-items:center;gap:6px;font-family:"Poppins",sans-serif;font-size:9px;font-weight:600;color:var(--ink)}
.follow span{margin-right:8px}
.social{width:28px;height:28px;border-radius:50%;border:1.5px solid var(--ink);display:inline-block}
.nav{position:absolute;display:flex;gap:0;font-family:"Poppins",sans-serif;font-weight:500;font-size:13px;color:var(--ink)}
.nav a{color:inherit;text-decoration:none;position:relative}
.nav a.active::after{content:"";position:absolute;left:0;right:0;bottom:-8px;height:2px;background:var(--ink)}
.hero{position:absolute;left:0;top:117px;width:1200px;height:463px;
  background:linear-gradient(180deg,#2c55c4 0%,#4c78d8 35%,#d7a7b8 62%,#2a2f5c 70%,#141a3a 100%)}
.hero h1{position:absolute;top:84px;width:100%;text-align:center;font-family:"Poppins",sans-serif;font-weight:700;font-size:31px;color:var(--white)}
.hero .btn-hero{position:absolute;left:538px;top:146px;width:124px;height:38px;border:2px solid var(--white);color:var(--white);
  font-family:"Poppins",sans-serif;font-weight:600;font-size:14px;display:flex;align-items:center;justify-content:center}
.dots{position:absolute;left:555px;top:424px;display:flex;gap:12px}
.dots i{width:8px;height:8px;border-radius:50%;background:var(--white)}
.dots i.on{background:#4aa64a}
.photo{position:absolute}
.btn{position:absolute;border:2px solid var(--brown);color:var(--brown);font-family:"Poppins",sans-serif;font-weight:600;font-size:12px;
  display:flex;align-items:center;justify-content:center;letter-spacing:.2px}
.section-title{position:absolute;left:0;width:1200px;text-align:center;font-family:"Libre Baskerville",serif;font-size:27px;color:var(--ink)}
.rule{position:absolute;width:38px;height:3px;background:#3b3128}
.welcome-pre{position:absolute;left:636px;top:634px;font-family:"Libre Baskerville",serif;font-size:18px;color:var(--ink)}
.welcome-title{position:absolute;left:636px;top:660px;font-family:"Libre Baskerville",serif;font-size:33px;color:var(--ink);white-space:nowrap}
.welcome-text{position:absolute;left:636px;top:740px;width:430px;font-size:16.5px;line-height:25.7px;color:var(--text)}
.service h3{position:absolute;font-family:"Libre Baskerville",serif;font-weight:400;font-size:17px;color:var(--ink);text-align:center;width:295px}
.service p{position:absolute;font-size:13.4px;line-height:17.8px;text-align:center;width:260px;color:var(--text)}
.quote{position:absolute;border:2px solid var(--frame);width:403px;height:316px}
.quote p{position:absolute;left:68px;top:32px;width:312px;font-size:13.2px;line-height:17.6px;color:var(--text)}
.quote b{position:absolute;left:69px;font-size:13px;font-weight:700;color:var(--ink);letter-spacing:.3px}
.avatar{position:absolute;width:83px;height:83px;border-radius:50%;background:linear-gradient(135deg,#7bb6d8,#3a7fa6 60%,#c49a7a)}
.post{position:absolute;top:2265px;width:224px;height:423px;background:var(--card)}
.post .thumb{position:absolute;left:0;top:0;width:224px;height:192px}
.post h4{position:absolute;left:19px;top:214px;width:190px;font-family:"Libre Baskerville",serif;font-weight:400;font-size:14.2px;line-height:17.5px;color:var(--ink)}
.post p{position:absolute;left:19px;top:266px;width:190px;font-size:12.2px;line-height:16px;color:var(--text)}
.post .btn{left:19px;top:371px;width:91px;height:28px;font-size:11px}
.footer-line{position:absolute;left:0;top:2828px;width:1200px;height:5px;border-top:2px solid var(--frame);border-bottom:2px solid var(--frame)}
.copyright{position:absolute;right:131px;top:2980px;font-size:12px;color:var(--ink)}
</style>
</head>
<body>
<div class="page">

  <!-- Header -->
  <header>
    <div class="brand-mark" style="left:150px;top:30px"></div>
    <div class="brand-name" style="left:227px;top:36px">Hop Bright Meadow!</div>
    <div class="brand-tag" style="left:229px;top:71px">Exploring Florida’s Natural Wonders</div>
    <div class="follow" style="left:901px;top:24px"><span>FOLLOW US</span><i class="social"></i><i class="social"></i><i class="social"></i></div>
    <nav class="nav" style="left:522px;top:76px">
      <a class="active" href="#" style="margin-right:28px">HOME</a>
      <a href="#" style="margin-right:30px">ABOUT US</a>
      <a href="#" style="margin-right:29px">WHAT WE DO</a>
      <a href="#" style="margin-right:29px">BLOG</a>
      <a href="#" style="margin-right:26px">TESTIMONIALS</a>
      <a href="#">CONTACT US</a>
    </nav>
  </header>

  <!-- Hero -->
  <section class="hero" role="img" aria-label="Photo of a Florida city skyline and bay at dusk">
    <h1>Exploring Florida’s Natural Wonders</h1>
    <div class="btn-hero">READ MORE</div>
    <div class="dots"><i></i><i></i><i class="on"></i><i></i><i></i></div>
  </section>

  <!-- Welcome -->
  <div class="photo" role="img" aria-label="Photo of a palm tree over the sea at a purple sunset"
       style="left:130px;top:636px;width:453px;height:355px;background:linear-gradient(180deg,#3a2a6e 0%,#8a4a9a 35%,#e27a8a 55%,#6a3a7a 75%,#3a2a5a 100%)"></div>
  <div class="welcome-pre">Welcome to</div>
  <div class="welcome-title">Hop Bright Meadow!</div>
  <div class="rule" style="left:636px;top:707px"></div>
  <p class="welcome-text">Come explore wild places and stunning scenery with me as I discover new and exciting eco-adventures and learn about the rare and unique wildlife and environments that make Florida so precious and extraordinary. I hope you can vicariously enjoy the wild and untamed beauty of Florida through my eyes, and learn some amazing things about nature on our explorations.</p>
  <div class="btn" style="left:639px;top:953px;width:115px;height:36px">READ MORE</div>

  <!-- What We Do -->
  <h2 class="section-title" style="top:1060px">What We Do</h2>
  <div class="rule" style="left:582px;top:1107px"></div>

  <div class="service">
    <div class="photo" role="img" aria-label="Photo of a green iguana on a rock" style="left:130px;top:1151px;width:295px;height:278px;background:linear-gradient(160deg,#8a7a5a,#5a6a3a 50%,#c4a884)"></div>
    <h3 style="left:130px;top:1458px">Lorem Ipsum is simp</h3>
    <p style="left:148px;top:1495px">Sed ut perspiciatis unde omnis iste natus error sit voluptatem accusantium dolo remque laudantium, totam rem aperiam, eaque ipsa qua.</p>
    <div class="btn" style="left:226px;top:1590px;width:104px;height:31px">READ MORE</div>
  </div>
  <div class="service">
    <div class="photo" role="img" aria-label="Photo of a small waterfall in a forest" style="left:453px;top:1151px;width:295px;height:278px;background:linear-gradient(160deg,#2a3a1e,#4a5a3a 45%,#9aa298 55%,#2a2e22)"></div>
    <h3 style="left:453px;top:1458px">Lorem Ipsum is simp</h3>
    <p style="left:470px;top:1495px">Sed ut perspiciatis unde omnis iste natus error sit voluptatem accusantium dolo remque laudantium, totam rem aperiam, eaque ipsa qua.</p>
    <div class="btn" style="left:548px;top:1590px;width:104px;height:31px">READ MORE</div>
  </div>
  <div class="service">
    <div class="photo" role="img" aria-label="Photo of a night heron standing by water" style="left:773px;top:1151px;width:295px;height:278px;background:linear-gradient(160deg,#5a6a3a,#6a7a5a 40%,#8a9aa8 70%,#c8ccd0)"></div>
    <h3 style="left:773px;top:1458px">Lorem Ipsum is simp</h3>
    <p style="left:790px;top:1495px">Sed ut perspiciatis unde omnis iste natus error sit voluptatem accusantium dolo remque laudantium, totam rem aperiam, eaque ipsa qua.</p>
    <div class="btn" style="left:868px;top:1590px;width:104px;height:31px">READ MORE</div>
  </div>

  <!-- Testimonials -->
  <h2 class="section-title" style="top:1697px">Testimonials</h2>
  <div class="rule" style="left:582px;top:1744px"></div>

  <svg class="abs" style="left:96px;top:1934px" width="18" height="28" viewBox="0 0 18 28"><path d="M14 3 L4 14 L14 25" fill="none" stroke="#8a8070" stroke-width="2.5"/></svg>
  <svg class="abs" style="left:1102px;top:1934px" width="18" height="28" viewBox="0 0 18 28"><path d="M4 3 L14 14 L4 25" fill="none" stroke="#8a8070" stroke-width="2.5"/></svg>

  <div class="quote" style="left:175px;top:1788px">
    <p>Hello nature lovers! I’m Maren Ostby, a wildlife educator, Florida Field Naturalist, nature writer and photographer, busy mama of three kiddos, a playful Havanese puppy, two very chubby guinea pigs, and a giant tree frog. I have a passion for all things nature and I adore living in Southwest Florida. I will always be a California girl, but from the moment I set foot in Florida, its wild beauty stole my heart. For the past 23 years, I have been fortunate to have some very unique and special experiences caring for many different species of animals and educating the public about wildlife and the environment.</p>
    <b style="top:272px">THEODORE</b>
  </div>
  <div class="avatar" role="img" aria-label="Portrait photo of the reviewer" style="left:130px;top:1818px"></div>

  <div class="quote" style="left:664px;top:1788px">
    <p>At vero eos et accusamus et iusto odio dignis simos ducimus qui blanditiis praesentium voluptatum deleniti atque corrupti quos dolores et quas molestias excepturi sint occaecati cupiditate non provident, similique sunt in culpa qui officia deserunt mollitia animi, id est laborum et dolorum fuga. Et harum quidem rerum facilis est et expedita distinctio. Nam libero tempore, cum soluta nobis est eligendi optio cumque nihil impedit quo minus id quod maxime placeat facere possimus, omnis voluptas assumenda est, omnis dolor repellendus.</p>
    <b style="top:272px">THEODORE</b>
  </div>
  <div class="avatar" role="img" aria-label="Portrait photo of the reviewer" style="left:619px;top:1818px"></div>

  <!-- Latest Blog -->
  <h2 class="section-title" style="top:2172px">Latest Blog</h2>
  <div class="rule" style="left:582px;top:2219px"></div>

  <svg class="abs" style="left:75px;top:2443px" width="18" height="28" viewBox="0 0 18 28"><path d="M14 3 L4 14 L14 25" fill="none" stroke="#8a8070" stroke-width="2.5"/></svg>
  <svg class="abs" style="left:1113px;top:2443px" width="18" height="28" viewBox="0 0 18 28"><path d="M4 3 L14 14 L4 25" fill="none" stroke="#8a8070" stroke-width="2.5"/></svg>

  <article class="post" style="left:130px">
    <div class="thumb" role="img" aria-label="Photo of a pale purple wildflower in grass" style="background:linear-gradient(160deg,#3e5a26,#5f7a3a 50%,#2e4220)"></div>
    <h4>Florida Field Naturalist Uplands Nature Journal</h4>
    <p>Since I was a child, my deepest spiritual connections with nature have come in the stillness as I hiked in the forest or listened to the waves crashing on the beach.</p>
    <div class="btn">READ MORE</div>
  </article>
  <article class="post" style="left:368px">
    <div class="thumb" role="img" aria-label="Photo of a yellow flower among green leaves" style="background:linear-gradient(160deg,#2e4a1e,#4d6a2e 50%,#2a3e1a)"></div>
    <h4>Environmental Ethics Statement:</h4>
    <p>As a Florida Field Naturalist, environmental interpreter, and nature writer, I will conduct my personal and professional life with integrity and strive to enlighten</p>
    <div class="btn">READ MORE</div>
  </article>
  <article class="post" style="left:607px">
    <div class="thumb" role="img" aria-label="Photo of tangled branches and hanging moss" style="background:linear-gradient(160deg,#4a5236,#7a7e6a 50%,#3a3e2a)"></div>
    <h4>FERN Cypress Dome Trails</h4>
    <p>FERN Cypress Dome Trails in Immokalee, Florida is part of a 60,000 acre conservation area protected by FERN Land &amp; Water Trust and managed by South Florida</p>
    <div class="btn">READ MORE</div>
  </article>
  <article class="post" style="left:845px">
    <div class="thumb" role="img" aria-label="Photo of an educational trail sign about watersheds" style="background:linear-gradient(180deg,#3e5a2a 0%,#3e5a2a 35%,#2f6aa8 40%,#5a9ad0 80%,#3e6a3a 100%)"></div>
    <h4>FERN Signage</h4>
    <p>A non-personal method of interpretation in the form of educational signs is posted on a large glass frame as you enter the trails. The posters and signs regarding activities, habitats, species,</p>
    <div class="btn">READ MORE</div>
  </article>

  <div class="btn" style="left:537px;top:2725px;width:124px;height:34px">VIEW ALL BLOG</div>

  <!-- Footer -->
  <footer>
    <div class="footer-line"></div>
    <div class="brand-mark" style="left:150px;top:2895px"></div>
    <div class="brand-name" style="left:228px;top:2901px">Hop Bright Meadow!</div>
    <div class="brand-tag" style="left:230px;top:2937px">Exploring Florida’s Natural Wonders</div>
    <div class="follow" style="left:898px;top:2893px"><span>FOLLOW US</span><i class="social"></i><i class="social"></i><i class="social"></i></div>
    <nav class="nav" style="left:533px;top:2942px">
      <a href="#" style="margin-right:26px">HOME</a>
      <a href="#" style="margin-right:32px">ABOUT US</a>
      <a href="#" style="margin-right:29px">WHAT WE DO</a>
      <a href="#" style="margin-right:29px">BLOG</a>
      <a href="#" style="margin-right:26px">TESTIMONIALS</a>
      <a href="#">CONTACT US</a>
    </nav>
    <div class="copyright">Copyright © 2020 All Rights Reserved</div>
  </footer>

</div>
</body>
</html>
```